Equipment Finance Specialist I work with companies who need the funds to buy their equipment

I would like a business card that stands out on the shelves. I want to be able to hand it to someone and say WOW. This card should have my logo.
You can put color into it I am very open on design and color

What my company does is we deal with dealerships that sell equipment such as Dump Trucks garbage trucks tractors trailers. Customers get referred to us and depending on their time in business we will ask for the following items

Companies that have been in business for more than two years we have a credit application program up to 250K . With this program we need the following items Credit application filled out(which is what I would like to be able for the customer to click on my website to get.) as well as three current month bank statements.

Deals over 250k we will need the following items

2 years business tax returns
2 years personal tax returns
Profit & Loss statement
Personal Financial Statement

what we do
100% FINANCING
SEASONAL PAYMENTS
LOAN BALLOON PAYMENTS
TRAC LEASING
LOW-INTEREST REFINANCING RATES
DEBT CONSOLIDATION

We specialize in creative financing solutions and offer a variety of reliable, flexible and expandable lending choices.

Target Market(s)

Trucking Companies

Industry/Entity Type

Trucking Company

Contact Information for Business Card

* $250,000 Application only Program
* Loans from $30,000 to 5,000,000
* Competitive Interest Rates

Font styles to use
Serif
Sans Serif

Colors

Designer to choose colors to be used in the design.

Requirements
Must have
• On the back of the card.
• * $250,000 Application only Program
• * Loans from $30,000 to 5,000,000
• My name, email, website. address
• * Competitive Interest Rates
• * 100% Financing
Nice to have
• I want my logo to pop on the card
• My logo is the great one I would like to use
Should not have
• I am up for your creativity as well

```html
<!DOCTYPE html>
<html lang="en">
<head>
<meta charset="utf-8">
<title>Ridgeline Capital – Business Card</title>
<link rel="stylesheet" href="https://fonts.googleapis.com/css2?family=Open+Sans:wght@400;600;700;800&display=swap">
<style>
  :root {
    --navy: #0f2a78;
    --navy-deep: #0a1f5c;
    --navy-light: #1a3c9a;
    --red: #d2193a;
    --ink: #333a48;
    --paper: #ffffff;
    --stage: #2a2a2c;
  }
  * { box-sizing: border-box; margin: 0; padding: 0; }
  html, body { width: 1200px; height: 892px; overflow: hidden; }
  body {
    background: var(--stage);
    font-family: "Open Sans", Arial, sans-serif;
    position: relative;
  }
  .card {
    position: absolute;
    width: 560px;
    height: 320px;
    overflow: hidden;
    box-shadow: 0 10px 30px rgba(0,0,0,.45);
  }

  /* Back */
  .card-back {
    left: 70px; top: 80px;
    background: radial-gradient(ellipse at 50% 35%, var(--navy-light), var(--navy-deep) 75%);
    color: var(--paper);
    text-align: center;
  }
  .back-brand {
    position: absolute; left: 0; right: 0; top: 96px;
    display: flex; align-items: center; justify-content: center; gap: 14px;
  }
  .brand-dot {
    width: 26px; height: 26px; border-radius: 50%;
    background: var(--paper);
  }
  .back-brand .brand-name {
    font-weight: 700; font-size: 34px; letter-spacing: .5px;
    color: var(--paper);
  }
  .back-offers {
    position: absolute; left: 0; right: 0; top: 226px;
    font-size: 15px; line-height: 1.45;
  }

  /* Front */
  .card-front {
    left: 570px; top: 480px;
    background: var(--paper);
    color: var(--ink);
  }
  .front-brand {
    position: absolute; right: 34px; top: 40px;
    display: flex; align-items: center; gap: 10px;
  }
  .front-brand .brand-dot { background: var(--navy); width: 22px; height: 22px; }
  .front-brand .brand-name {
    font-weight: 800; font-size: 28px; color: var(--navy);
  }
  .divider {
    position: absolute; left: 30px; right: 66px; top: 118px;
    height: 1px; background: #3a3f4a;
  }
  .address {
    position: absolute; right: 34px; top: 130px;
    text-align: right; font-size: 14px; line-height: 1.35; color: #555b66;
  }
  .holder {
    position: absolute; left: 30px; top: 186px;
  }
  .holder-name { font-size: 22px; font-weight: 800; color: var(--navy); line-height: 1.1; }
  .holder-title { font-size: 15px; color: var(--red); letter-spacing: .3px; }
  .holder-rule { width: 210px; height: 1px; background: #555; margin: 6px 0 8px; }
  .contact { list-style: none; font-size: 15px; color: #555b66; }
  .contact li { display: flex; align-items: center; gap: 10px; line-height: 1.45; }
  .contact svg { width: 15px; height: 15px; fill: var(--navy); flex: none; }
  .band { position: absolute; fill: var(--navy); }
  .web {
    position: absolute; right: 30px; top: 253px;
    font-size: 14px; color: var(--paper);
  }
</style>
</head>
<body>

<section class="card card-back" aria-label="Card back">
  <div class="back-brand">
    <span class="brand-dot"></span>
    <span class="brand-name">Ridgeline Capital</span>
  </div>
  <p class="back-offers">
    $250,000 Application only Program • Loans from $30,000 to 5,000,000<br>
    Competitive Interest Rates • 100% Financing
  </p>
</section>

<section class="card card-front" aria-label="Card front">
  <div class="front-brand">
    <span class="brand-dot"></span>
    <span class="brand-name">Ridgeline Capital</span>
  </div>
  <div class="divider"></div>
  <p class="address">1720 Harbor Point Road<br>Lakeview, NY 11560</p>

  <svg class="band" width="560" height="320" viewBox="0 0 560 320" style="left:0;top:0">
    <path d="M350 248 L560 248 L560 320 L0 320 L0 306 L340 306 L340 258 Z"/>
  </svg>
  <span class="web">www.ridgelinecapital.com</span>

  <div class="holder">
    <div class="holder-name">MARCUS HALE</div>
    <div class="holder-title">PRESIDENT</div>
    <div class="holder-rule"></div>
    <ul class="contact">
      <li><svg viewBox="0 0 24 24"><path d="M6.6 10.8a15 15 0 0 0 6.6 6.6l2.2-2.2a1 1 0 0 1 1-.25 11.4 11.4 0 0 0 3.6.57 1 1 0 0 1 1 1V20a1 1 0 0 1-1 1A17 17 0 0 1 3 4a1 1 0 0 1 1-1h3.5a1 1 0 0 1 1 1c0 1.25.2 2.45.57 3.57a1 1 0 0 1-.25 1z"/></svg>555 0142 7781</li>
      <li><svg viewBox="0 0 24 24"><path d="M2 5h20v14H2z M2 5l10 8 10-8" /></svg>marcus@ridgelinecapital.com</li>
    </ul>
  </div>
</section>

</body>
</html>
```